HOME PAGE AND AND SECONDARY DESIGN FOR INTERNAL PAGES

Construction company looking for an easy to navagate professional serious greyscale website with a good clean feel simple clean menu and responsive friendly design. Our main clientele is commercial properties business owners and investors of rental properties. This website is going to be static HTML5 and would need multiple sizing files for clean fast rendering. Clean and accurate design files a must so if your experienced awesome modern greyscale designer let's get started I need this done as soon as possible.

Industry/Entity Type

construction, electrical, plumbing, commercial build outs

Number of Pages Required

2 page

Font styles to use
Sans Serif

Colors

Designer to choose only greyscale colors for use in the design.

Requirements
Must have
• Main Menu... Home, Services, Projects, About our team

```html
<!DOCTYPE html>
<html lang="en">
<head>
<meta charset="utf-8">
<title>Ironline Builders of Texas LLC</title>
<link href="https://fonts.googleapis.com/css2?family=Oswald:wght@400;500&family=Roboto:wght@400;500&display=swap" rel="stylesheet">
<style>
:root{
  --ink:#333;
  --ink-soft:#555;
  --muted:#8a8a8a;
  --line:#e2e2e2;
  --paper:#fff;
  --band:#f4f4f4;
  --footer:#595959;
  --footer-text:#f2f2f2;
  --photo-dark:#6a6a6a;
  --photo-light:#b5b5b5;
}
*{margin:0;padding:0;box-sizing:border-box}
html,body{width:1200px;height:3445px;overflow:hidden;background:var(--paper)}
body{position:relative;font-family:'Roboto',sans-serif;color:var(--ink)}
.abs{position:absolute}
.photo{background:linear-gradient(160deg,var(--photo-light),var(--photo-dark))}
.center{left:0;width:1200px;text-align:center}

/* header */
.site-header{position:absolute;top:0;left:0;width:1200px;height:123px;background:var(--paper)}
.brand{position:absolute;display:flex;align-items:center;gap:10px}
.brand-mark{width:22px;height:22px;background:var(--ink-soft)}
.brand-name{font-family:'Roboto',sans-serif;font-weight:500;font-size:15px;line-height:18px;letter-spacing:1px;color:var(--ink-soft);text-transform:uppercase}
.main-nav{position:absolute;top:52px;left:457px;display:flex;gap:35px;font-size:15px;font-weight:500;color:var(--ink-soft)}
.main-nav a{color:inherit;text-decoration:none;position:relative}
.main-nav a.active::after{content:"";position:absolute;left:-2px;right:-2px;bottom:-9px;height:2px;background:var(--ink)}
.btn-outline{position:absolute;border:2px solid var(--ink-soft);display:flex;align-items:center;justify-content:center;font-size:14px;font-weight:500;color:var(--ink-soft);background:var(--paper)}

/* hero */
.hero{position:absolute;top:123px;left:0;width:1200px;height:514px;background:linear-gradient(100deg,#5c5c5c,#8c8c8c 45%,#7a7a7a 70%,#3e3e3e)}
.hero-title{top:282px;font-family:'Oswald',sans-serif;font-weight:500;font-size:32px;color:#fff}
.hero-text{top:340px;font-size:18px;line-height:30px;color:#fff}
.btn-light{position:absolute;background:#fff;display:flex;align-items:center;justify-content:center;font-size:14px;font-weight:500;color:var(--ink)}
.dots{position:absolute;top:606px;left:927px;display:flex;gap:7px}
.dots span{width:10px;height:10px;border:1.5px solid #fff;border-radius:50%}
.dots span.on{background:#fff}

/* section titles */
.ghost{font-family:'Oswald',sans-serif;font-weight:500;font-size:82px;line-height:1;color:transparent;background:linear-gradient(#e6e6e6,rgba(230,230,230,0));-webkit-background-clip:text;background-clip:text}
.title{font-family:'Oswald',sans-serif;font-weight:500;font-size:40px;line-height:1;color:var(--ink)}

.about-text{top:830px;left:138px;width:924px;text-align:center;font-size:15.5px;line-height:26.5px;color:var(--ink-soft)}

.band{position:absolute;left:0;width:1200px;background:var(--band)}

/* services */
.service{position:absolute;width:320px;text-align:center}
.service h3{font-size:17px;font-weight:500;line-height:24px;color:var(--ink-soft);margin-top:10px}
.service p{font-size:14px;line-height:24px;color:var(--muted);margin-top:12px}
.plus{width:40px;height:40px;border-radius:50%;background:#fff;box-shadow:0 4px 10px rgba(0,0,0,.15);margin:18px auto 0;display:flex;align-items:center;justify-content:center}

/* team */
.member{position:absolute;top:2032px;width:231px;height:257px}
.member-name{position:absolute;left:17px;top:232px;width:197px;height:48px;background:#fff;box-shadow:0 6px 14px rgba(0,0,0,.12);display:flex;align-items:center;justify-content:center;font-size:19px;color:var(--ink-soft)}

/* footer */
.site-footer{position:absolute;top:3081px;left:0;width:1200px;height:364px;background:var(--footer);color:var(--footer-text)}
.site-footer h4{font-size:17px;font-weight:500;letter-spacing:.3px}
.links li{list-style:none;font-size:14px;height:39.5px;display:flex;align-items:center;gap:18px}
.links li::before{content:"";width:12px;height:12px;border-radius:50%;background:#aaa}
.contact-item{position:absolute;left:0;display:flex;gap:16px}
.contact-item b{display:block;font-size:14px;font-weight:500}
.contact-item span{display:block;font-size:11.5px;line-height:22px}
.signup{position:absolute;left:805px;top:104px;width:283px;height:46px;border:2px solid #fff;display:flex}
.signup .field{flex:1;background:#fff;font-size:13px;color:var(--ink-soft);display:flex;align-items:center;padding-left:15px}
.signup .go{width:106px;background:var(--footer);display:flex;align-items:center;justify-content:center;font-size:13px}
.social{position:absolute;top:175px;left:805px;display:flex;gap:7px}
.social span{width:44px;height:44px;border-radius:50%;background:#777}
.social span:first-child{background:#fff}
.rule{position:absolute;left:111px;top:307px;width:977px;height:1px;background:#777}
.copy{position:absolute;top:324px;left:0;width:1200px;text-align:center;font-size:13px}
</style>
</head>
<body>

<header class="site-header">
  <div class="brand" style="left:111px;top:38px">
    <div class="brand-mark"></div>
    <div class="brand-name">Ironline Builders<br>of Texas LLC</div>
  </div>
  <nav class="main-nav">
    <a class="active" href="#">HOME</a><a href="#">SERVICES</a><a href="#">PROJECTS</a><a href="#">ABOUT OUR TEAM</a>
  </nav>
  <a class="btn-outline" style="left:954px;top:37px;width:134px;height:49px">CONTACT US</a>
</header>

<section class="hero" role="img" aria-label="Construction workers on scaffolding and engineers reviewing plans on site"></section>
<h1 class="abs center hero-title">IRONLINE BUILDERS OF TEXAS LLC</h1>
<p class="abs center hero-text">Lorem ipsum dolor sit amet consectetur adipiscing sed<br>do eiusmod temp doloreorea.</p>
<a class="btn-light" style="left:532px;top:421px;width:136px;height:49px">GET STARTED</a>
<div class="dots"><span></span><span class="on"></span><span></span><span></span></div>
<svg class="abs" style="left:1013px;top:605px" width="77" height="14"><line x1="0" y1="7" x2="74" y2="7" stroke="#fff" stroke-width="1"/><polyline points="67,1 74,7 67,13" fill="none" stroke="#fff" stroke-width="1.5"/></svg>

<!-- about -->
<div class="abs center ghost" style="top:712px">ABOUT US</div>
<h2 class="abs center title" style="top:757px">ABOUT US</h2>
<p class="abs about-text">Lorem ipsum dolor sit amet, consectetur adipiscing elit, sed do eiusmod tempor incididunt ut labore et dolore magna aliqua. Ut enim ad minim veniam, quis nostrud exercitation ullamco laboris nisi ut aliquip ex ea commodo consequat. Duis aute irure dolor in reprehenderit in voluptate velit esse cillum dolore eu fugiat nulla pariatur. Excepteur sint occaecat cupidatat non proident, sunt in culpa qui officia deserunt mollit laboexercitation ullamco laboris nisi ut aliquip ex ea.</p>
<a class="btn-outline" style="left:532px;top:971px;width:136px;height:48px">LEARN MORE</a>

<!-- services -->
<div class="band" style="top:1113px;height:711px"></div>
<div class="abs center ghost" style="top:1183px">OUR SERVICES</div>
<h2 class="abs center title" style="top:1230px">OUR SERVICES</h2>

<svg class="abs" style="left:0;top:1315px" width="1200" height="270" aria-hidden="true">
  <defs>
    <linearGradient id="g" x1="0" y1="0" x2="1" y2="1"><stop offset="0" stop-color="#c4c4c4"/><stop offset="1" stop-color="#5e5e5e"/></linearGradient>
    <mask id="cut"><rect width="1200" height="270" fill="#fff"/>
      <circle cx="265" cy="400" r="185" fill="#000"/><circle cx="599" cy="400" r="185" fill="#000"/><circle cx="934" cy="400" r="185" fill="#000"/></mask>
  </defs>
  <g mask="url(#cut)" fill="url(#g)">
    <circle cx="265" cy="155" r="155" role="img" aria-label="Engineer reviewing plans on a laptop"/>
    <circle cx="599" cy="155" r="155" role="img" aria-label="Workers inspecting rebar on a construction site"/>
    <circle cx="934" cy="155" r="155" role="img" aria-label="Business handshake over blueprints"/>
  </g>
</svg>

<div class="service" style="left:105px;top:1556px"><h3>LOREM IPSUM<br>DOLOR SIT AMET</h3><p>Sed ut perspiciatis unde omnis iste nat<br>us error sit voluptatem accusantium<br>doloremque laudantea.</p><div class="plus"><svg width="12" height="12"><path d="M6 0v12M0 6h12" stroke="#333" stroke-width="2.5"/></svg></div></div>
<div class="service" style="left:439px;top:1556px"><h3>LOREM IPSUM<br>DOLOR SIT AMET</h3><p>Sed ut perspiciatis unde omnis iste nat<br>us error sit voluptatem accusantium<br>doloremque laudantea.</p><div class="plus"><svg width="12" height="12"><path d="M6 0v12M0 6h12" stroke="#333" stroke-width="2.5"/></svg></div></div>
<div class="service" style="left:774px;top:1556px"><h3>LOREM IPSUM<br>DOLOR SIT AMET</h3><p>Sed ut perspiciatis unde omnis iste nat<br>us error sit voluptatem accusantium<br>doloremque laudantea.</p><div class="plus"><svg width="12" height="12"><path d="M6 0v12M0 6h12" stroke="#333" stroke-width="2.5"/></svg></div></div>

<!-- team -->
<div class="abs center ghost" style="top:1896px">ABOUT OUR TEAM</div>
<h2 class="abs center title" style="top:1948px">ABOUT OUR TEAM</h2>
<div class="member" style="left:111px"><div class="photo" style="height:257px" role="img" aria-label="Portrait of team member"></div><div class="member-name">JOHN SMITH</div></div>
<div class="member" style="left:360px"><div class="photo" style="height:257px" role="img" aria-label="Portrait of team member"></div><div class="member-name">JOHN SMITH</div></div>
<div class="member" style="left:609px"><div class="photo" style="height:257px" role="img" aria-label="Portrait of team member"></div><div class="member-name">JOHN SMITH</div></div>
<div class="member" style="left:858px"><div class="photo" style="height:257px" role="img" aria-label="Portrait of team member"></div><div class="member-name">JOHN SMITH</div></div>

<!-- projects -->
<div class="band" style="top:2428px;height:653px"></div>
<div class="abs center ghost" style="top:2490px">OUR PROJECTS</div>
<h2 class="abs center title" style="top:2542px">OUR PROJECTS</h2>
<div class="abs photo" style="left:111px;top:2630px;width:232px;height:180px" role="img" aria-label="Modern apartment building"></div>
<div class="abs photo" style="left:360px;top:2630px;width:231px;height:180px" role="img" aria-label="Engineers reviewing plans on site"></div>
<div class="abs photo" style="left:609px;top:2630px;width:231px;height:180px" role="img" aria-label="Workers under a highway overpass"></div>
<div class="abs photo" style="left:858px;top:2630px;width:230px;height:379px" role="img" aria-label="Crane over a building site with workers"></div>
<div class="abs photo" style="left:111px;top:2828px;width:480px;height:181px" role="img" aria-label="Steel frame construction site with cranes"></div>
<div class="abs photo" style="left:609px;top:2828px;width:231px;height:181px" role="img" aria-label="Residential apartment blocks"></div>

<!-- footer -->
<footer class="site-footer">
  <div class="brand" style="left:111px;top:124px">
    <div class="brand-mark" style="background:#fff"></div>
    <div class="brand-name" style="color:#fff">Ironline Builders<br>of Texas LLC</div>
  </div>

  <div class="abs" style="left:347px;top:58px">
    <h4>QUICK LINKS</h4>
    <ul class="links" style="margin-top:12px">
      <li>Home</li><li>Services</li><li>Projects</li><li>About Our Team</li><li>Contact Us</li>
    </ul>
  </div>

  <div class="abs" style="left:545px;top:58px;width:230px;height:240px">
    <h4>CONTACT INFO</h4>
    <div class="contact-item" style="top:42px">
      <svg width="14" height="16"><path d="M7 1a5 5 0 0 1 5 5c0 4-5 9-5 9S2 10 2 6a5 5 0 0 1 5-5z" fill="#aaa"/><circle cx="7" cy="6" r="2" fill="#595959"/></svg>
      <div><b>ADDRESS:</b><span>Lorum Ipsum Dolore Sed do,<br>United States</span></div>
    </div>
    <div class="contact-item" style="top:125px">
      <svg width="14" height="16"><path d="M3 2l3 0 1 4-2 1c1 2 2 3 4 4l1-2 4 1 0 3c-6 1-12-5-11-11z" fill="#aaa"/></svg>
      <div><b>PHONE:</b><span>+1 (000) 000 0000</span></div>
    </div>
    <div class="contact-item" style="top:181px">
      <svg width="14" height="16"><rect x="0" y="3" width="14" height="10" fill="#aaa"/><polyline points="0,3 7,9 14,3" fill="none" stroke="#595959" stroke-width="1.5"/></svg>
      <div><b>EMAIL:</b><span>info@ironlinebuilders.com</span></div>
    </div>
  </div>

  <h4 class="abs" style="left:805px;top:58px">NEWSLETTER SIGNUP</h4>
  <div class="signup"><div class="field">Email Address</div><div class="go">SIGN UP</div></div>
  <div class="social" aria-label="Social links"><span></span><span></span><span></span></div>

  <div class="rule"></div>
  <p class="copy">© 2023 IRONLINE BUILDERS OF TEXAS &nbsp;|&nbsp; All Rights Reserved</p>
</footer>

</body>
</html>
```